Brightwave Reach - Business Card

We need a business card for a Social Media Marketing company that specializes in online marketing for small businesses in Canada using common Social Media platforms such as Pixlora, Chatterly, Blinkpost & Quibber.

I have uploaded a copy of our logo which I would like utilized in the business card. We would like the business card to be modern yet classy design.

Our website is www.brightwavereach.ca

Industry/Entity Type

Marketing

Contact Information for Business Card

Email: info@brightwavereach.ca
Website: www.brightwavereach.ca
Telephone: 604-555-0193

Colors

Designer to choose colors to be used in the design.

Requirements
Must have
• Social Media icons on reverse
• Please add some designs with color.

```html
<!DOCTYPE html>
<html lang="en">
<head>
<meta charset="utf-8">
<title>Brightwave Reach – Business Card</title>
<link rel="stylesheet" href="https://fonts.googleapis.com/css2?family=Open+Sans:wght@400;600;700;800&display=swap">
<style>
  :root {
    --backdrop: #2a2b2d;
    --card: #f4f4f4;
    --card-edge: #e4e4e4;
    --ink: #2f3336;
    --band: #3f4447;
    --band-light: #555b5f;
    --muted: #8a8e91;
    --rule: #5a5f62;
  }
  * { box-sizing: border-box; margin: 0; padding: 0; }
  html, body {
    width: 1200px; height: 960px; overflow: hidden;
    background: var(--backdrop);
    font-family: "Open Sans", Arial, sans-serif;
  }
  .card {
    position: absolute; left: 220px; width: 760px; height: 434px;
    background: linear-gradient(135deg, #fbfbfb 0%, var(--card) 55%, var(--card-edge) 100%);
    border-radius: 3px; overflow: hidden;
    box-shadow: 0 14px 30px rgba(0,0,0,.45);
  }
  .card--back { top: 40px; }
  .card--front { top: 486px; }

  /* Back */
  .back-name {
    position: absolute; left: 0; right: 0; top: 120px;
    text-align: center; font-weight: 800; font-size: 44px;
    letter-spacing: 2px; text-transform: uppercase; color: var(--ink);
  }
  .social-row {
    position: absolute; left: 60px; right: 60px; top: 300px;
    display: flex; align-items: center; gap: 18px;
  }
  .social-row .rule { flex: 1; height: 1px; background: var(--rule); }
  .social-item { display: flex; align-items: center; gap: 7px; font-size: 15px; font-weight: 600; color: var(--ink); }
  .social-item .dot { width: 22px; height: 22px; border: 2px solid var(--ink); border-radius: 50%; }

  /* Front */
  .band {
    position: absolute; left: 0; right: 0; top: 0; height: 54px;
    background: linear-gradient(90deg, var(--band) 0%, var(--band-light) 100%);
  }
  .contact { position: absolute; left: 50px; top: 205px; color: var(--ink); }
  .contact .person { font-weight: 700; font-size: 23px; text-transform: uppercase; }
  .contact .role { font-size: 18px; color: var(--muted); text-transform: uppercase; margin-bottom: 8px; }
  .contact ul { list-style: none; }
  .contact li { display: flex; align-items: center; gap: 12px; font-size: 17px; line-height: 28px; }
  .contact svg { width: 15px; height: 15px; fill: var(--ink); flex: none; }
  .brand {
    position: absolute; right: 56px; top: 130px;
    display: flex; align-items: center; gap: 16px;
  }
  .brand .mark { width: 22px; height: 22px; background: var(--ink); }
  .brand .wordmark {
    font-weight: 800; font-size: 42px; line-height: 46px;
    text-transform: uppercase; color: var(--ink); letter-spacing: 1px; text-align: right;
  }
</style>
</head>
<body>

<section class="card card--back" aria-label="Card back">
  <div class="back-name">Brightwave Reach</div>
  <div class="social-row">
    <span class="rule"></span>
    <span class="social-item"><span class="dot"></span>Chatterly</span>
    <span class="social-item"><span class="dot"></span>Pixlora</span>
    <span class="social-item"><span class="dot"></span>Quibber</span>
    <span class="rule"></span>
  </div>
</section>

<section class="card card--front" aria-label="Card front">
  <div class="band"></div>
  <div class="contact">
    <div class="person">Daniel Reyes</div>
    <div class="role">CEO/Founder</div>
    <ul>
      <li>
        <svg viewBox="0 0 16 16"><path d="M3 2h3l1.5 3.5-2 1.3a9 9 0 0 0 3.7 3.7l1.3-2L14 10v3a1 1 0 0 1-1 1A12 12 0 0 1 2 3a1 1 0 0 1 1-1z"/></svg>
        604-555-0193
      </li>
      <li>
        <svg viewBox="0 0 16 16"><path d="M1 3h14v1.2L8 9 1 4.2zM1 6l7 4.8L15 6v7H1z"/></svg>
        info@brightwavereach.ca
      </li>
      <li>
        <svg viewBox="0 0 16 16"><circle cx="8" cy="8" r="7"/><path d="M3 6h10M3 10h10M8 1c-2.5 3-2.5 11 0 14M8 1c2.5 3 2.5 11 0 14" stroke="#f4f4f4" stroke-width="1" fill="none"/></svg>
        www.brightwavereach.ca
      </li>
    </ul>
  </div>
  <div class="brand">
    <span class="mark"></span>
    <div class="wordmark">Brightwave<br>Reach</div>
  </div>
</section>

</body>
</html>
```